Whitcombe Business Card Design

The name of the business is Dario Whitcombe, CPA LLC
The service that we offer is Accounting, Tax & Consulting Services. I need it to have the following items:
Dario Whitcombe, Principal
Phone Number
Email Address
Physical Address

I have attached the company logo, one in black and one in white. Please provide a design in black background and the other in white background. Please include "Accounting, Tax & Consulting Services". I want the business card to be clean and very professional.

```html
<!DOCTYPE html>
<html lang="en">
<head>
<meta charset="utf-8">
<title>Dario Whitcombe, CPA LLC — Business Cards</title>
<link rel="stylesheet" href="https://fonts.googleapis.com/css2?family=Montserrat:wght@500;600&family=Arimo:wght@400&display=swap">
<style>
  :root {
    --backdrop: #cfcecb;
    --card: #ffffff;
    --brand-red: #a3161d;
    --ink: #2f2f31;
    --muted: #8e8e90;
    --soft-gray: #f2f2f2;
  }
  * { box-sizing: border-box; margin: 0; padding: 0; }
  html, body {
    width: 1200px; height: 801px; overflow: hidden;
    background: var(--backdrop);
  }
  .stage {
    width: 1200px; height: 801px;
    display: flex; align-items: center; justify-content: center; gap: 48px;
  }
  .card {
    position: relative;
    width: 540px; height: 309px;
    background: var(--card);
    border-bottom: 6px solid var(--brand-red);
    box-shadow: 0 10px 24px rgba(0,0,0,0.18);
    overflow: hidden;
  }
  .card__band {
    position: absolute; top: 0; right: 0;
    width: 190px; height: 100%;
    background: var(--soft-gray);
  }
  /* front: contact side */
  .contact { position: absolute; left: 44px; top: 40px; font-family: "Arimo", Arial, sans-serif; color: var(--ink); }
  .wordmark {
    font-family: "Montserrat", sans-serif; font-weight: 600;
    font-size: 19px; letter-spacing: 0.5px; text-transform: uppercase;
    color: var(--ink); white-space: nowrap;
  }
  .tagline {
    font-family: "Montserrat", sans-serif; font-weight: 500;
    font-size: 10.5px; letter-spacing: 2.6px; text-transform: uppercase;
    color: var(--muted); margin-top: 3px;
  }
  .person { margin-top: 34px; }
  .person__name {
    font-family: "Montserrat", sans-serif; font-weight: 600;
    font-size: 21px; color: var(--brand-red); text-transform: uppercase; letter-spacing: 0.5px;
  }
  .person__role { font-size: 13px; margin-top: 2px; }
  .address { margin-top: 18px; font-size: 13px; line-height: 1.4; }
  .details { margin-top: 12px; list-style: none; font-size: 13px; line-height: 1.55; }
  .details li { display: flex; align-items: center; gap: 8px; }
  .details svg { width: 11px; height: 11px; fill: var(--brand-red); flex: none; }
  /* back: brand side */
  .brand { position: absolute; left: 46px; top: 110px; display: flex; align-items: center; gap: 16px; }
  .brand__square { width: 34px; height: 34px; background: var(--brand-red); flex: none; }
  .brand .wordmark { font-size: 22px; }
  .brand .tagline { font-size: 12px; letter-spacing: 3.4px; }
  .services {
    position: absolute; left: 0; right: 0; bottom: 56px; text-align: center;
    font-family: "Arimo", Arial, sans-serif; font-size: 15px; color: var(--ink);
  }
</style>
</head>
<body>
<main class="stage">
  <section class="card card--contact">
    <div class="card__band"></div>
    <div class="contact">
      <div class="wordmark">Dario Whitcombe, CPA LLC</div>
      <div class="tagline">Certified Public Accountant</div>
      <div class="person">
        <div class="person__name">Dario Whitcombe</div>
        <div class="person__role">Principal</div>
      </div>
      <address class="address" style="font-style:normal">
        1480 N Harlow Avenue<br>Brenwick County 6042
      </address>
      <ul class="details">
        <li><svg viewBox="0 0 12 12" aria-hidden="true"><path d="M2.4 0.8l2 2-1 1.4a6 6 0 0 0 4.4 4.4l1.4-1 2 2-1.4 1.6C5.4 11.6 0.4 6.6 0.8 2.2z"/></svg>555-318-2960</li>
        <li><svg viewBox="0 0 12 12" aria-hidden="true"><path d="M0.5 2.5h11v7h-11z M0.5 2.5l5.5 4 5.5-4" fill="none" stroke="#a3161d" stroke-width="1.3"/></svg>info@whitcombecpa.com</li>
        <li><svg viewBox="0 0 12 12" aria-hidden="true"><circle cx="6" cy="6" r="5" fill="none" stroke="#a3161d" stroke-width="1.3"/><path d="M1 6h10M6 1c-2.5 3-2.5 7 0 10M6 1c2.5 3 2.5 7 0 10" fill="none" stroke="#a3161d" stroke-width="1"/></svg>www.whitcombecpa.com</li>
      </ul>
    </div>
  </section>

  <section class="card card--brand">
    <div class="card__band"></div>
    <div class="brand">
      <div class="brand__square"></div>
      <div>
        <div class="wordmark">Dario Whitcombe, CPA LLC</div>
        <div class="tagline">Certified Public Accountant</div>
      </div>
    </div>
    <p class="services">Accounting, Tax &amp; Consulting Services</p>
  </section>
</main>
</body>
</html>
```